Using attached logo that has been created

Business card with logo that's attached. Maybe with water or the cartoon van in background. Looking for it to not be so plain and not too white.
Information to include;
Rodney Ashcombe
(555) 218-7730
Info@bramleypipeworks.example
www.bramleypipeworks.example
License # 4627195
Looking forward to the designs u come up with.
Thank you!
-Delphine
Target Market(s)
Plumbing
Industry/Entity Type
Plumbing
Contact Information for Business Card
Listed above

```html
<!DOCTYPE html>
<html lang="en">
<head>
<meta charset="utf-8">
<title>Bramley Pipeworks – Business Card</title>
<link rel="stylesheet" href="https://fonts.googleapis.com/css2?family=Montserrat:wght@400;500;700&display=swap">
<style>
  :root {
    --backdrop: #e4e4e4;
    --card-white: #fbfbfb;
    --card-yellow: #fbc217;
    --brand-blue: #1a56b8;
    --text-grey: #6b6b6b;
    --icon-orange: #f2a81d;
    --mascot-blue: #2f6fc4;
    --mascot-tan: #9a8462;
  }
  * { box-sizing: border-box; margin: 0; padding: 0; }
  html, body {
    width: 1200px; height: 801px; overflow: hidden;
    background: var(--backdrop);
    font-family: "Montserrat", Arial, sans-serif;
  }
  .stage {
    width: 1200px; height: 801px;
    display: flex; align-items: center; justify-content: center; gap: 40px;
  }
  .card {
    width: 540px; height: 309px;
    border-bottom: 4px solid var(--brand-blue);
    box-shadow: 0 8px 22px rgba(0,0,0,0.14);
    position: relative;
    overflow: hidden;
  }
  .card--back {
    background: var(--card-white);
    display: flex; align-items: center; justify-content: center;
    padding: 0 36px;
  }
  .identity { text-align: right; padding-right: 20px; white-space: nowrap; }
  .identity__name {
    color: var(--brand-blue); font-weight: 700; font-size: 17px;
    letter-spacing: 0.4px; text-transform: uppercase;
  }
  .identity__license {
    color: var(--text-grey); font-size: 13px; margin-top: 5px; letter-spacing: 0.3px;
  }
  .divider { width: 1.5px; height: 56px; background: var(--brand-blue); opacity: .75; flex: none; }
  .contacts { list-style: none; padding-left: 20px; }
  .contacts__item {
    display: flex; align-items: center; gap: 7px; white-space: nowrap;
    color: var(--text-grey); font-size: 12px; line-height: 21px;
  }
  .contacts__icon { width: 11px; height: 11px; flex: none; }
  .card--front {
    background: var(--card-yellow);
    display: flex; flex-direction: column; align-items: center; justify-content: center;
  }
  .mascot-area {
    width: 120px; height: 150px; border-radius: 6px;
    background: linear-gradient(180deg, var(--mascot-blue) 0%, var(--mascot-blue) 55%, var(--mascot-tan) 100%);
  }
  .brand-name {
    margin-top: 12px; color: var(--brand-blue);
    font-weight: 700; font-size: 24px; letter-spacing: 0.5px; text-transform: uppercase;
  }
</style>
</head>
<body>
<main class="stage">
  <section class="card card--back">
    <div class="identity">
      <p class="identity__name">Rodney Ashcombe</p>
      <p class="identity__license">License # 4627195</p>
    </div>
    <div class="divider"></div>
    <ul class="contacts">
      <li class="contacts__item">
        <svg class="contacts__icon" viewBox="0 0 24 24"><path fill="var(--icon-orange)" d="M6.6 10.8a15.5 15.5 0 0 0 6.6 6.6l2.2-2.2a1 1 0 0 1 1-.25 11.4 11.4 0 0 0 3.6.6 1 1 0 0 1 1 1V20a1 1 0 0 1-1 1A17 17 0 0 1 3 4a1 1 0 0 1 1-1h3.5a1 1 0 0 1 1 1c0 1.25.2 2.45.57 3.57a1 1 0 0 1-.25 1z"/></svg>
        (555) 218-7730
      </li>
      <li class="contacts__item">
        <svg class="contacts__icon" viewBox="0 0 24 24"><rect x="2" y="5" width="20" height="14" rx="2" fill="var(--icon-orange)"/><path d="M3 6l9 7 9-7" stroke="#fff" stroke-width="2" fill="none"/></svg>
        Info@bramleypipeworks.example
      </li>
      <li class="contacts__item">
        <svg class="contacts__icon" viewBox="0 0 24 24"><circle cx="12" cy="12" r="10" fill="var(--icon-orange)"/><path d="M2 12h20M12 2c3 3 3 17 0 20M12 2c-3 3-3 17 0 20" stroke="#fff" stroke-width="1.5" fill="none"/></svg>
        www.bramleypipeworks.example
      </li>
    </ul>
  </section>

  <section class="card card--front">
    <div class="mascot-area" role="img" aria-label="Cartoon mascot of a plumber holding a pipe wrench and a circular saw"></div>
    <p class="brand-name">Bramley Pipeworks</p>
  </section>
</main>
</body>
</html>
```